Brightmill Data Works

Our company is about IT hardwares and IT solutions. IT hardware such as PC, RAMS, storage and servers. IT solutions such as project management, BA. We are also selling new technology too.

Target Market(s)

Consumer, Small to Medium Business, Corporate

Requirements
Must have
• The business card must have the following:
• Name:
• Title:
• Contact Number:
• Email address:
• Website:
• Color: Must match the logo color upgrade

```html
<!DOCTYPE html>
<html lang="en">
<head>
<meta charset="utf-8">
<title>Brightmill Data Works – Business Card</title>
<link rel="stylesheet" href="https://fonts.googleapis.com/css2?family=Open+Sans:wght@400;600;700&display=swap">
<style>
  :root {
    --backdrop: #3b3b3d;
    --card: #1f2022;
    --amber: #e08a22;
    --amber-deep: #c96f16;
    --white: #f4f4f4;
    --rule: #6b6b6b;
  }
  * { margin: 0; padding: 0; box-sizing: border-box; }
  html, body {
    width: 1200px; height: 1108px; overflow: hidden;
    background: var(--backdrop);
    font-family: "Open Sans", Arial, sans-serif;
  }
  .stage {
    width: 1200px; height: 1108px;
    display: flex; justify-content: center; align-items: center; gap: 60px;
  }
  .card {
    position: relative;
    width: 420px; height: 680px;
    background: var(--card);
    border-radius: 24px;
    color: var(--white);
    text-align: center;
  }
  .brand {
    position: absolute; left: 0; right: 0;
    display: flex; flex-direction: column; align-items: center; gap: 18px;
  }
  .brand-dot {
    width: 34px; height: 34px; border-radius: 50%;
    background: var(--amber);
  }
  .brand-name {
    font-weight: 700; font-size: 34px; line-height: 1.15;
    letter-spacing: 1px; text-transform: uppercase;
    color: var(--white);
  }
  .card-front .brand { top: 120px; }
  .card-back .brand { top: 210px; }

  .person { position: absolute; top: 372px; left: 0; right: 0; }
  .person-name {
    color: var(--amber); font-size: 27px; font-weight: 400;
    text-transform: uppercase; letter-spacing: 0.5px;
  }
  .person-title {
    font-size: 17px; text-transform: uppercase; margin-top: 2px;
  }

  .divider {
    position: absolute; top: 478px; left: 90px; right: 90px;
    display: flex; align-items: center; gap: 6px;
  }
  .divider-line { flex: 1; height: 1px; background: var(--rule); }
  .icon {
    width: 20px; height: 20px; border-radius: 50%;
    background: var(--amber);
    display: flex; align-items: center; justify-content: center;
  }
  .icon svg { width: 12px; height: 12px; }

  .contacts {
    position: absolute; top: 510px; left: 0; right: 0;
    list-style: none; font-size: 18px; line-height: 1.6;
    text-transform: uppercase;
  }
  .tagline {
    position: absolute; bottom: 92px; left: 0; right: 0;
    font-size: 18px; text-transform: uppercase;
  }
</style>
</head>
<body>
<main class="stage">
  <section class="card card-front">
    <div class="brand">
      <span class="brand-dot"></span>
      <span class="brand-name">Brightmill<br>Data Works</span>
    </div>
    <div class="person">
      <p class="person-name">Daniel Carter</p>
      <p class="person-title">Managing Director</p>
    </div>
    <div class="divider">
      <span class="divider-line"></span>
      <span class="icon">
        <svg viewBox="0 0 12 12"><path d="M3 1.5l1.6 2.3-1 1.1c.6 1.3 1.5 2.2 2.6 2.7l1.1-1 2.3 1.6-.8 1.9C5.5 9.9 2.1 6.5 1.1 2.3z" fill="#1f2022"/></svg>
      </span>
      <span class="icon">
        <svg viewBox="0 0 12 12"><rect x="1.5" y="3" width="9" height="6" rx="1" fill="#1f2022"/><path d="M1.8 3.4L6 6.4l4.2-3" stroke="#e08a22" stroke-width="0.9" fill="none"/></svg>
      </span>
      <span class="icon">
        <svg viewBox="0 0 12 12"><circle cx="6" cy="6" r="4.2" fill="none" stroke="#1f2022" stroke-width="1.2"/><path d="M1.8 6h8.4M6 1.8c-2 2.4-2 6 0 8.4M6 1.8c2 2.4 2 6 0 8.4" stroke="#1f2022" stroke-width="0.9" fill="none"/></svg>
      </span>
      <span class="divider-line"></span>
    </div>
    <ul class="contacts">
      <li>555 010 2847</li>
      <li>hello@brightmilldata.com</li>
      <li>www.brightmilldata.com</li>
    </ul>
  </section>

  <section class="card card-back">
    <div class="brand">
      <span class="brand-dot"></span>
      <span class="brand-name">Brightmill<br>Data Works</span>
    </div>
    <p class="tagline">IT Hardwares and IT Solutions</p>
  </section>
</main>
</body>
</html>
```